Executive Business Card for Healthcare Company [Need Today]

I need a business card design for a healthcare company. The only branding the company has thus far is a logo. The cards will be utilized by company executives. The design I envision will be vibrant and appealing but with a corporate feel. They shouldn't be too casual or playful. I would like to complete this project TODAY if possible.

Target Market(s)

Healthcare vendors, other executives in healthcare and pharmaceuticals

Industry/Entity Type

Pharmaceutical

Contact Information for Business Card

See attachment

Font styles to use
Serif
Sans Serif

Colors

Designer to choose colors to be used in the design.

```html
<!DOCTYPE html>
<html lang="en">
<head>
<meta charset="utf-8">
<title>Calder Therapeutics – Business Card</title>
<link rel="stylesheet" href="https://fonts.googleapis.com/css2?family=Questrial&display=swap">
<style>
  :root {
    --teal: #33bfc6;
    --teal-soft: #5cc39a;
    --grey-text: #6b6b70;
    --grey-rule: #707075;
    --card: #ffffff;
    --backdrop: #e9e9eb;
  }
  html, body {
    margin: 0;
    padding: 0;
    width: 1200px;
    height: 902px;
    overflow: hidden;
    background: var(--backdrop);
    font-family: "Questrial", "Century Gothic", sans-serif;
  }
  .business-card {
    position: absolute;
    left: 80px;
    top: 155px;
    width: 1040px;
    height: 592px;
    background: var(--card);
    border-radius: 24px;
    overflow: hidden;
    box-shadow: 0 6px 24px rgba(0,0,0,0.12);
  }
  .footer-rule {
    position: absolute;
    left: 0;
    right: 0;
    top: 486px;
    height: 5px;
    background: var(--grey-rule);
  }
  .footer-band {
    position: absolute;
    left: 0;
    right: 0;
    top: 500px;
    bottom: 0;
    background: var(--teal);
  }
  .brand {
    position: absolute;
    left: 81px;
    top: 212px;
    display: flex;
    align-items: center;
    gap: 22px;
  }
  .brand-dot {
    width: 116px;
    height: 116px;
    border: 4px solid var(--teal-soft);
    border-radius: 50%;
    box-sizing: border-box;
  }
  .brand-name {
    color: var(--teal);
    line-height: 1;
    text-align: right;
  }
  .brand-name .word {
    display: block;
    font-size: 50px;
  }
  .brand-name .sub {
    display: block;
    font-size: 27px;
    margin-top: 4px;
  }
  .divider {
    position: absolute;
    left: 519px;
    top: 144px;
    width: 2px;
    height: 260px;
    background: var(--teal);
  }
  .contact {
    position: absolute;
    left: 578px;
    top: 142px;
    color: var(--grey-text);
  }
  .contact .name {
    margin: 0;
    font-size: 30px;
    font-weight: 400;
    color: var(--teal);
    line-height: 34px;
  }
  .contact .title {
    margin: 0;
    font-size: 25px;
    line-height: 30px;
  }
  .contact .address {
    margin: 28px 0 0;
    font-size: 25px;
    line-height: 32px;
    font-style: normal;
  }
  .contact .lines {
    list-style: none;
    margin: 18px 0 0;
    padding: 0;
  }
  .contact .lines li {
    display: flex;
    align-items: center;
    gap: 6px;
    font-size: 25px;
    line-height: 32px;
  }
  .icon {
    width: 28px;
    height: 28px;
    flex: none;
  }
</style>
</head>
<body>
  <div class="business-card">
    <div class="footer-rule"></div>
    <div class="footer-band"></div>

    <div class="brand">
      <div class="brand-dot"></div>
      <div class="brand-name">
        <span class="word">calder</span>
        <span class="sub">therapeutics</span>
      </div>
    </div>

    <div class="divider"></div>

    <div class="contact">
      <h1 class="name">Martin Lowe</h1>
      <p class="title">Senior Director of Marketing</p>
      <address class="address">518 W Linden Avenue<br>Marion, OH 43302</address>
      <ul class="lines">
        <li>
          <svg class="icon" viewBox="0 0 28 28" aria-label="Mobile">
            <circle cx="14" cy="14" r="12" fill="none" stroke="var(--teal-soft)" stroke-width="2"/>
            <rect x="10" y="7" width="8" height="14" rx="1.5" fill="none" stroke="var(--teal-soft)" stroke-width="1.8"/>
          </svg>
          555-214-7730
        </li>
        <li>
          <svg class="icon" viewBox="0 0 28 28" aria-label="Office phone">
            <circle cx="14" cy="14" r="12" fill="var(--teal-soft)"/>
            <path d="M8 12 Q14 7 20 12 L18 14 L16 12 L12 12 L10 14 Z M9 15 H19 V20 H9 Z" fill="#fff"/>
          </svg>
          555-380-6142
        </li>
        <li>
          <svg class="icon" viewBox="0 0 28 28" aria-label="Email">
            <circle cx="14" cy="14" r="12" fill="var(--teal-soft)"/>
            <rect x="8" y="9" width="12" height="10" fill="#fff"/>
            <path d="M8 9 L14 15 L20 9" fill="none" stroke="var(--teal-soft)" stroke-width="1.5"/>
          </svg>
          mlowe@calderrx.com
        </li>
      </ul>
    </div>
  </div>
</body>
</html>
```